Varnex Consulting Business card design.

See our website www.varnexconsulting.example which will give you a good idea of what we are about. The font is called 'Play'.

I'd like a standout business card in keeping with the themes and branding on the website

Target Market(s)

professionals. HR directors

Industry/Entity Type

Business

Contact Information for Business Card

Varnex Consulting PO Box 3172 Merrowdale NSW 2291 1300 485 193 Gavin Threlkeld Principal email: career@varnexconsulting.example ABN: 71203948865

Font styles to use
Other font styles liked:
• Play

Requirements
Must have
• Must have same design colours and branding as website.
• On back I'd prefer a list of the things we do which appears below the name at the header on the website

```html
<!DOCTYPE html>
<html lang="en">
<head>
<meta charset="utf-8">
<title>Varnex Consulting – Business Cards</title>
<link href="https://fonts.googleapis.com/css2?family=Play:wght@400;700&display=swap" rel="stylesheet">
<style>
  :root {
    --navy: #14293d;
    --blue: #2a8fdd;
    --paper: #fbfbfb;
    --ink: #1d2a36;
    --backdrop: #a9a7a7;
  }
  * { margin: 0; padding: 0; box-sizing: border-box; }
  html, body { width: 1200px; height: 1200px; overflow: hidden; }
  body {
    background: var(--backdrop);
    font-family: 'Play', sans-serif;
    color: var(--ink);
    position: relative;
  }
  .card {
    position: absolute;
    left: 240px;
    width: 720px;
    height: 420px;
    background: var(--paper);
    overflow: hidden;
  }
  .card--front { top: 110px; }
  .card--back { top: 640px; }

  .brand {
    position: absolute;
    display: flex;
    align-items: center;
    gap: 14px;
    white-space: nowrap;
    line-height: 1;
  }
  .brand-mark { width: 16px; height: 16px; background: var(--blue); flex: none; }
  .brand-name {
    font-family: 'Play', sans-serif;
    font-weight: 700;
    color: var(--navy);
  }
  .services {
    position: absolute;
    font-family: 'Play', sans-serif;
    color: var(--blue);
    white-space: nowrap;
    letter-spacing: 1px;
    line-height: 1;
  }
  .services .sep { color: var(--navy); margin: 0 6px; letter-spacing: 0; }

  /* Front */
  .card--front .brand { left: 0; right: 0; justify-content: center; top: 134px; }
  .card--front .brand-name { font-size: 50px; }
  .card--front .services { left: 0; right: 0; text-align: center; top: 198px; font-size: 15px; }
  .front-url {
    position: absolute; left: 0; right: 0; top: 347px;
    display: flex; justify-content: center; align-items: center; gap: 14px;
    font-size: 18px;
  }
  .front-url svg { display: block; }
  .accent { color: var(--blue); }

  /* Back */
  .side-band { position: absolute; left: 0; top: 0; width: 60px; height: 100%; background: var(--navy); }
  .side-stripe { position: absolute; left: 60px; top: 0; width: 7px; height: 100%; background: var(--blue); }
  .card--back .brand { left: 92px; top: 60px; }
  .card--back .brand-name { font-size: 44px; }
  .card--back .services { left: 92px; top: 118px; font-size: 14.5px; }
  .person-name { position: absolute; left: 92px; top: 196px; font-size: 25px; font-weight: 700; color: var(--navy); }
  .person-title { position: absolute; left: 92px; top: 231px; font-size: 17px; }
  .contact-list { position: absolute; left: 92px; top: 284px; list-style: none; font-size: 18px; }
  .contact-list li { display: flex; align-items: center; height: 24px; }
  .contact-list .icon { width: 16px; height: 16px; margin-right: 19px; }
  .postal { position: absolute; left: 92px; top: 360px; font-size: 18px; }
  .abn { position: absolute; right: 40px; top: 284px; font-size: 18px; height: 24px; display: flex; align-items: center; }
  .abn .label { color: var(--blue); margin-right: 5px; }
</style>
</head>
<body>

<section class="card card--front" aria-label="Card front">
  <div class="brand"><span class="brand-mark"></span><span class="brand-name">Varnex Consulting</span></div>
  <div class="services">Executive Search<span class="sep">|</span>Careers<span class="sep">|</span>Mentoring<span class="sep">|</span>Leadership<span class="sep">|</span>Transition</div>
  <div class="front-url">
    <svg width="40" height="4" viewBox="0 0 40 4"><path d="M0 2 L40 0.5 L40 3.5 Z" fill="var(--blue)"/></svg>
    <span>www.<span class="accent">varnexconsulting</span>.example</span>
    <svg width="40" height="4" viewBox="0 0 40 4"><path d="M40 2 L0 0.5 L0 3.5 Z" fill="var(--blue)"/></svg>
  </div>
</section>

<section class="card card--back" aria-label="Card back">
  <div class="side-band"></div>
  <div class="side-stripe"></div>
  <div class="brand"><span class="brand-mark"></span><span class="brand-name">Varnex Consulting</span></div>
  <div class="services">Executive Search<span class="sep">|</span>Careers<span class="sep">|</span>Mentoring<span class="sep">|</span>Leadership<span class="sep">|</span>Transition</div>

  <div class="person-name">Gavin Threlkeld</div>
  <div class="person-title">Principal</div>

  <ul class="contact-list">
    <li>
      <svg class="icon" viewBox="0 0 16 16" aria-hidden="true"><path d="M1 5 Q8 1 15 5 L13 7 L11 5.5 L5 5.5 L3 7 Z M4 8 H12 L14 14 H2 Z" fill="var(--blue)"/><circle cx="8" cy="10.5" r="1.6" fill="var(--paper)"/></svg>
      <span>1300 485 193</span>
    </li>
    <li>
      <svg class="icon" viewBox="0 0 16 16" aria-hidden="true"><circle cx="8" cy="8" r="6.5" fill="var(--blue)"/><g fill="none" stroke="var(--paper)" stroke-width="1"><ellipse cx="8" cy="8" rx="2.8" ry="6.5"/><path d="M1.5 8 H14.5 M2.5 5 H13.5 M2.5 11 H13.5 M8 1.5 V14.5"/></g></svg>
      <span>www.<span class="accent">varnexconsulting</span>.example</span>
    </li>
    <li>
      <svg class="icon" viewBox="0 0 16 16" aria-hidden="true"><rect x="1" y="3.5" width="14" height="9.5" fill="var(--blue)"/><path d="M1 3.5 L8 9 L15 3.5 M1 13 L6 8 M15 13 L10 8" fill="none" stroke="var(--paper)" stroke-width="1.1"/></svg>
      <span>career@varnexconsulting.example</span>
    </li>
  </ul>
  <div class="postal">PO Box 3172 Merrowdale NSW 2291</div>
  <div class="abn"><span class="label">ABN:</span>71203948865</div>
</section>

</body>
</html>
```